Corvane Business Cards

Front of business card will have logo, name, address, & telephone number. Back of card will have a list of services provided - Roads, Substation Pads, Temporary Pads, Site Pads, Land Leveling, Powerline Row Cleaning, Land Clearing, Gates, Fencing, Construction Entrances, Excavation, Trenching, Underground Utilities, Directional Boring, Pile Driving. We are a construction company that uses heavy equipment like bulldozers, motor graders/blades, dump trucks, backhoes, hydro axes, & skid loaders. We build roads, pads, & install electric utility lines & waterlines underground. This logo is new. The word "Construction" can be smaller as uploaded 2 example edited logos. We will be using this card design for many employees.
Target Market(s)
Industrial Electric Powerline, Wind Turbine, Solar Panel, & Water Utility companies.
Contact Information for Business Card
Name/Position - Dwayne Halster - Owner
Address: 4875 FM 309
Calder Springs, NM 88204
Phone number - (575) 482-5096

```html
<!DOCTYPE html>
<html lang="en">
<head>
<meta charset="utf-8">
<title>Corvane Business Cards</title>
<link rel="stylesheet" href="https://fonts.googleapis.com/css2?family=Open+Sans:wght@400;600&family=Arimo:wght@400;700&display=swap">
<style>
  :root {
    --maroon: #3d121b;
    --white: #ffffff;
    --backdrop: #4a4a4c;
    --ink-light: #f3eaec;
  }
  * { box-sizing: border-box; margin: 0; padding: 0; }
  html, body {
    width: 1200px; height: 1015px; overflow: hidden;
    background: var(--backdrop);
  }
  .sheet {
    width: 1200px; height: 1015px;
    display: flex; flex-direction: column; align-items: center; justify-content: center;
    gap: 22px;
  }
  .card {
    position: relative;
    width: 820px; height: 469px;
    background: var(--maroon);
    overflow: hidden;
    box-shadow: 0 10px 24px rgba(0,0,0,0.35);
  }
  .card__white {
    position: absolute; left: 0; top: 0; height: 100%; width: 440px;
    background: var(--white);
    clip-path: polygon(0 0, 340px 0, 340px 150px, 440px 190px, 340px 230px, 340px 100%, 0 100%);
  }
  .logo {
    position: absolute; left: 30px; top: 0; width: 300px; height: 100%;
    display: flex; flex-direction: column; align-items: center; justify-content: center; gap: 10px;
    color: var(--maroon);
    font-family: "Arimo", Arial, sans-serif; font-weight: 700;
  }
  .logo__row { display: flex; align-items: center; gap: 12px; }
  .logo__square { width: 34px; height: 34px; background: var(--maroon); }
  .logo__name { font-size: 44px; letter-spacing: 1px; text-transform: uppercase; }
  .logo__sub { font-size: 22px; letter-spacing: 2px; text-transform: uppercase; }

  .services {
    position: absolute; left: 372px; right: 20px; top: 0; height: 100%;
    display: flex; flex-direction: column; justify-content: center; gap: 56px;
    font-family: "Open Sans", Arial, sans-serif; font-size: 17px; line-height: 1.35;
    color: var(--ink-light);
    white-space: nowrap;
  }
  .services__list { padding-left: 80px; }

  .contact {
    position: absolute; left: 460px; right: 20px; top: 80px;
    font-family: "Arimo", Arial, sans-serif; color: var(--ink-light);
    white-space: nowrap;
  }
  .contact__name { font-size: 30px; font-weight: 700; text-transform: uppercase; line-height: 1; }
  .contact__role { font-size: 19px; margin-top: 4px; }
  .contact__phone { font-size: 22px; font-weight: 700; margin-top: 18px; padding-left: 30px; }
  .contact__address { font-size: 19px; line-height: 1.3; margin-top: 24px; padding-left: 30px; }
</style>
</head>
<body>
<main class="sheet">
  <section class="card card--back">
    <div class="card__white"></div>
    <div class="logo">
      <div class="logo__row"><span class="logo__square"></span><span class="logo__name">Corvane</span></div>
    </div>
    <div class="services">
      <p class="services__intro">We build roads, pads install electric<br>utility lines waterlines underground.</p>
      <p class="services__list">We are a construction company that<br>uses heavy equipment<br>like bulldozers | motor graders/blades<br>dump trucks | backhoes<br>hydro axes &amp; skid loaders.</p>
    </div>
  </section>

  <section class="card card--front">
    <div class="card__white"></div>
    <div class="logo">
      <div class="logo__row"><span class="logo__square"></span><span class="logo__name">Corvane</span></div>
      <span class="logo__sub">Construction</span>
    </div>
    <div class="contact">
      <p class="contact__name">Dwayne Halster</p>
      <p class="contact__role">Owner</p>
      <p class="contact__phone">P: (575) 482-5096</p>
      <p class="contact__address">4875 FM 309<br>Calder Springs, NM 88204</p>
    </div>
  </section>
</main>
</body>
</html>
```